Redesign a Start-Up Dating Website

Website: https://morvelique.com.
Make sure the design has an island style theme.
I would like the 7 pages of my website to have a new and professional look. I want the same colors to remain, but I want a creative look for all the pages. This is a dating website that is in the startup stage. So, I want to give my entire website a custom makeover. I want something that will stand out from the other dating sites. Something that will attract more people to want to use my services, and hopefully get new members.
Target Market(s)
Dating
Industry/Entity Type
Dating
Coding
Coded - Design and coding required
Number of Pages Required
5+ page
Font styles to use
Other font styles liked:
- Decorative, San Serif
Requirements
Must have
- The design must have the original colors and a stylish font to go along. The design must be creative, welcoming, and professional. I would like an island style theme for the website. This is a dating website so make sure that the design is tailored to that aspect.
Nice to have
- It would be nice to have a decorative font and a professional style on all the pages. Make sure the design will be mobile responsive and friendly for all the pages on the website.
Should not have
- The design should not be bland and uncreative.

```html
<!DOCTYPE html>
<html lang="en">
<head>
<meta charset="utf-8">
<title>Morvelique – Dating is easy</title>
<link href="https://fonts.googleapis.com/css2?family=Open+Sans:wght@300;400;600;700;800&display=swap" rel="stylesheet">
<style>
:root{
  --teal:#33b39e;
  --teal-soft:#62b9a3;
  --teal-deep:#2aa08c;
  --orange:#f28a1f;
  --orange-deep:#e27c12;
  --purple:#6a3d9c;
  --ink:#222;
  --muted:#666;
  --white:#fff;
}
*{box-sizing:border-box;margin:0;padding:0}
html,body{width:1200px;height:2761px;overflow:hidden}
body{font-family:"Open Sans",Arial,sans-serif;color:var(--ink);background:var(--white)}
.wrap{width:1000px;margin:0 auto;position:relative}

/* header */
.site-header{height:120px;display:flex;align-items:center;background:var(--white);box-shadow:0 3px 8px rgba(0,0,0,.12);position:relative;z-index:2}
.site-header .wrap{display:flex;align-items:center}
.brand{display:flex;align-items:center;gap:10px;font-weight:700;font-size:34px;color:var(--teal);letter-spacing:-.5px;white-space:nowrap}
.brand-dot{width:50px;height:50px;border-radius:50%;background:var(--orange);flex:none}
.main-nav{display:flex;gap:21px;margin-left:auto;margin-right:30px;font-size:11.5px;font-weight:600;text-transform:uppercase;white-space:nowrap}
.main-nav a{color:var(--ink);text-decoration:none}
.main-nav a.active{color:var(--orange)}
.account{display:flex;gap:8px;flex:none}
.account a{font-size:10.5px;font-weight:600;padding:5px 10px;border:2px solid var(--teal);color:var(--teal);text-decoration:none;border-radius:2px;text-transform:uppercase;white-space:nowrap}
.account a.register{background:var(--teal);color:var(--white)}

/* hero */
.hero{height:546px;position:relative;text-align:center;color:var(--white);
  background:linear-gradient(180deg,#d9dcdc 0%,#b9bcb8 40%,#8b8470 72%,#6a5f4d 100%)}
.hero-title{position:absolute;top:200px;left:0;right:0;font-size:56px;font-weight:800;letter-spacing:.5px;text-shadow:0 2px 6px rgba(0,0,0,.35);line-height:1.1}
.hero-sub{position:absolute;top:268px;left:0;right:0;font-size:14px;font-weight:600;text-transform:uppercase;text-shadow:0 1px 3px rgba(0,0,0,.4)}
.btn-orange{display:inline-block;background:var(--orange);color:var(--white);font-weight:600;font-size:19px;text-transform:uppercase;text-decoration:none;width:190px;height:47px;line-height:47px}
.hero .btn-orange{position:absolute;top:318px;left:505px}
.dots{position:absolute;top:456px;left:0;right:0;display:flex;justify-content:center;gap:8px}
.dots span{width:15px;height:15px;border:2px solid var(--white);border-radius:50%}
.dots span.on{background:var(--white)}

/* quick search */
.quick-search{height:223px;background:var(--teal-soft);color:var(--white)}
.quick-search h2{text-align:center;font-size:32px;font-weight:700;padding-top:34px}
.search-row{display:flex;align-items:flex-end;margin-top:24px}
.field{margin-right:25px}
.field label{display:block;font-size:12px;text-transform:uppercase;margin-bottom:8px}
.select{height:40px;background:var(--white);color:#333;font-size:12.5px;text-transform:uppercase;display:flex;align-items:center;justify-content:space-between;padding:0 12px}
.select::after{content:"";width:6px;height:6px;border-right:1.5px solid #777;border-bottom:1.5px solid #777;transform:rotate(45deg);margin-top:-4px}
.btn-search{margin-left:auto;width:143px;height:44px;background:var(--teal);color:var(--white);font-size:20px;font-weight:600;display:flex;align-items:center;justify-content:center;text-transform:uppercase}

/* welcome */
.welcome{height:587px;text-align:center}
.section-title{font-size:37px;font-weight:300;text-transform:uppercase;color:#333}
.welcome .section-title{padding-top:52px}
.welcome .lead{width:800px;margin:14px auto 0;font-size:13px;line-height:22px;color:#555}
.steps{display:flex;justify-content:space-between;width:978px;margin:70px auto 0}
.step{width:300px;display:flex;flex-direction:column;align-items:center}
.step-icon{width:147px;height:147px;border-radius:50%;border:5px solid var(--white);box-shadow:0 0 0 4px currentColor;display:flex;align-items:center;justify-content:center}
.step-icon svg{width:64px;height:64px}
.step-icon.teal{background:var(--teal);color:var(--teal)}
.step-icon.purple{background:var(--purple);color:var(--purple)}
.step-icon.orange{background:var(--orange);color:var(--orange)}
.step h3{font-size:24px;font-weight:600;margin-top:24px}
.step p{width:270px;font-size:12.5px;line-height:23px;color:#555;margin-top:10px}

/* promo */
.promo{height:449px;text-align:center;color:var(--white);
  background:radial-gradient(ellipse at 50% 30%,#f7a544 0%,var(--orange) 45%,var(--orange-deep) 80%,#c96a0d 100%)}
.promo h2{font-size:42px;font-weight:300;padding-top:80px}
.promo p{font-size:12.5px;line-height:24px;margin-top:22px}
.btn-outline{display:inline-block;margin-top:48px;width:186px;height:46px;line-height:43px;border:2px solid rgba(255,255,255,.8);color:var(--white);font-size:18px;text-transform:uppercase;text-decoration:none}

/* members */
.members{height:491px;text-align:center}
.members .section-title{padding-top:62px}
.member-list{display:flex;justify-content:space-between;margin-top:54px}
.member{width:170px;display:flex;flex-direction:column;align-items:center}
.avatar{width:160px;height:160px;border-radius:50%}
.member .name{color:var(--orange);font-weight:700;font-size:14px;margin-top:20px}
.member .city{font-size:13.5px;font-weight:600;margin-top:8px}

/* footer */
.site-footer{height:345px;background:var(--teal);color:var(--white)}
.footer-cols{display:flex;padding-top:44px;height:274px}
.footer-cols h4{font-size:18px;font-weight:600;text-transform:uppercase;margin-bottom:18px}
.col-links{width:362px}
.col-links ul{list-style:none;display:grid;grid-template-columns:196px 1fr;row-gap:11px;font-size:14px}
.col-contact{width:312px;font-size:15px;line-height:28px}
.col-contact p{width:240px}
.col-contact .row{display:flex;align-items:center;gap:10px;font-size:14px}
.col-contact svg{width:14px;height:14px;fill:var(--white)}
.col-news{flex:1}
.col-news p{font-size:14px;margin-bottom:14px}
.subscribe{display:flex;height:38px}
.subscribe span{flex:1;background:var(--white);color:#aaa;font-size:13px;padding:0 14px;display:flex;align-items:center}
.subscribe b{width:106px;background:var(--orange);font-weight:600;font-size:14px;display:flex;align-items:center;justify-content:center}
.social{display:flex;gap:12px;margin-top:20px}
.social span{width:38px;height:38px;border-radius:50%;background:var(--white)}
.footer-bottom{border-top:1px solid rgba(255,255,255,.5);padding-top:20px;font-size:13.5px}
</style>
</head>
<body>

<header class="site-header">
  <div class="wrap">
    <div class="brand"><span class="brand-dot"></span>Morvelique</div>
    <nav class="main-nav">
      <a class="active" href="#">Home</a><a href="#">Search</a><a href="#">Members</a><a href="#">Extras</a><a href="#">About</a><a href="#">Premium</a><a href="#">Contact</a>
    </nav>
    <div class="account"><a href="#">Login</a><a class="register" href="#">Register</a></div>
  </div>
</header>

<section class="hero" role="img" aria-label="Photo of a couple sitting on a bench by the sea at sunset">
  <h1 class="hero-title">DATING IS EASY WITH MORVELIQUE</h1>
  <p class="hero-sub">Sign-up for a 30 days free trial enjoy all the benefits Morvelique has to offer with a full membership.</p>
  <a class="btn-orange" href="#">Join up free</a>
  <div class="dots"><span class="on"></span><span></span><span></span><span></span></div>
</section>

<section class="quick-search">
  <div class="wrap">
    <h2>QUICK SEARCH</h2>
    <div class="search-row">
      <div class="field" style="width:180px"><label>I am:</label><div class="select">Man</div></div>
      <div class="field" style="width:180px"><label>Seeking a:</label><div class="select">Woman</div></div>
      <div class="field" style="width:105px"><label>Age:</label><div class="select">18</div></div>
      <div class="field" style="width:105px"><label>To:</label><div class="select">99</div></div>
      <div class="field" style="width:160px"><label>Country:</label><div class="select">India</div></div>
      <div class="btn-search">Search</div>
    </div>
  </div>
</section>

<section class="welcome">
  <h2 class="section-title">Welcome to Morvelique</h2>
  <p class="lead">Nemo enim ipsam voluptatem quia voluptas sit aspernatur aut odit aut fugit, sed quia consequuntur magni dolores eos qui ratione voluptatem sequi nesciunt</p>
  <div class="steps">
    <div class="step">
      <div class="step-icon teal"><svg viewBox="0 0 64 64" fill="#fff"><circle cx="32" cy="20" r="12"/><path d="M10 54c0-12 10-20 22-20s22 8 22 20z"/></svg></div>
      <h3>Create a Profile</h3>
      <p>Let people know all about you; the good and the quirky-show the world your true colors and find someone with the same unique qualities as you.</p>
    </div>
    <div class="step">
      <div class="step-icon purple"><svg viewBox="0 0 64 64" fill="#fff"><path d="M32 56 8 32C1 24 4 10 16 10c7 0 12 5 16 10 4-5 9-10 16-10 12 0 15 14 8 22z"/></svg></div>
      <h3>Find Matches</h3>
      <p>Browse other users and feel the excitement of getting your first message and getting to know potential dates in a safe and fun environment.</p>
    </div>
    <div class="step">
      <div class="step-icon orange"><svg viewBox="0 0 64 64" fill="#fff"><circle cx="21" cy="10" r="6"/><path d="M15 19h12l5 20h-6v18h-4V43h-2v14h-4V39h-6z"/><circle cx="44" cy="10" r="6"/><path d="M38 19h12v20h-3v18h-4V42h-2v15h-4V39h-3z"/></svg></div>
      <h3>Start Dating</h3>
      <p>Once you've found your potential soulmate, it's time to meet up and say 'Hello' to the start of your journey together</p>
    </div>
  </div>
</section>

<section class="promo" role="img" aria-label="Sunset photo of a couple silhouetted against an orange sky">
  <div class="wrap">
    <h2>Starts Dating Singles Today!</h2>
    <p>Morvelique aims to provide a straight-forward, easy-to-use online dating service. I won't over-complicate things or reduce the amount of people you can talk to with algorithms. I know that sometimes, opposites attract and sparks can fly with the last person you thought you'd be interested in-so I won't hide anybody from you.There is no discrimination on this dating site, it's not only about accepting young singles. I think everybody deserves love and should be given the same opportunity to find their true match. Especially when it comes to finding your perfect match, a broader community is always better. My trusted 24-hour service means that there are singles online at all times whether you're a night-owl or a morning person, there's always someone to connect with.</p>
    <a class="btn-outline" href="#">Join up free</a>
  </div>
</section>

<section class="members">
  <h2 class="section-title">Morvelique Members</h2>
  <div class="wrap member-list">
    <div class="member"><div class="avatar" role="img" aria-label="Member photo" style="background:radial-gradient(circle,#f4d27a,#d9982c)"></div><div class="name">Minima Veniam 28</div><div class="city">New York</div></div>
    <div class="member"><div class="avatar" role="img" aria-label="Member photo" style="background:radial-gradient(circle,#cfc6c0,#5a4a42)"></div><div class="name">Quis Nostrum 24</div><div class="city">Culpa Qui</div></div>
    <div class="member"><div class="avatar" role="img" aria-label="Member photo" style="background:radial-gradient(circle,#c9b8a4,#7a5f48)"></div><div class="name">Tempora Incidunt 23</div><div class="city">Officia Deserunt</div></div>
    <div class="member"><div class="avatar" role="img" aria-label="Member photo" style="background:radial-gradient(circle,#7f97a3,#3c5666)"></div><div class="name">Rem Aperiam 27</div><div class="city">Est Laborum</div></div>
    <div class="member"><div class="avatar" role="img" aria-label="Member photo" style="background:radial-gradient(circle,#c7c7c7,#3a3535)"></div><div class="name">Eaque Ipsa 21</div><div class="city">Mollit Anim</div></div>
  </div>
</section>

<footer class="site-footer">
  <div class="wrap">
    <div class="footer-cols">
      <div class="col-links">
        <h4>Quick Links</h4>
        <ul><li>Morvelique</li><li>Premium</li><li>About</li><li>Register</li><li>Contact</li><li>Search</li><li>Login</li><li></li><li>Members</li></ul>
      </div>
      <div class="col-contact">
        <h4>Contact Info</h4>
        <p>Morvelique, Coral Bay, Palm Islands, 00921</p>
        <div class="row"><svg viewBox="0 0 16 16"><path d="M3 1h3l1.5 4-2 1.5c1 2 2 3 4 4l1.5-2 4 1.5v3c0 1-1 2-2 2C6 15 1 10 1 3c0-1 1-2 2-2z"/></svg>(+01) 555-0147</div>
        <div class="row"><svg viewBox="0 0 16 16"><path d="M1 3h14v10H1z M1 3l7 6 7-6" stroke="#33b39e" stroke-width="1"/></svg>contact@morvelique.com</div>
      </div>
      <div class="col-news">
        <h4>Sign up for Newsletters</h4>
        <p>Please sign up here for latest news</p>
        <div class="subscribe"><span>EMAIL ADDRESS</span><b>SUBSCRIBE</b></div>
        <div class="social"><span></span><span></span><span></span><span></span></div>
      </div>
    </div>
    <div class="footer-bottom">© 2017 MORVELIQUE.&nbsp; All right reserved . Term of Use</div>
  </div>
</footer>

</body>
</html>
```